Fun, Clean Business Card For Family Focused Travel Agency

I need a business card using specific colors and fonts as in the uploaded files. Ideally, I would like a large image of the logo on the back and all the contact info on the front. Maybe the stars/dots somewhere in a flowy form.

I do want it the contact information to be clear and easy to read. I don't want it to look too busy. Maybe even a bit minimalist.

I plan or ordering the ROUNDED CORNER business cards from Cardwell Press, so please consider that in your design.

Target Market(s)

Families with children, couples, groups of friends

Contact Information for Business Card

Marla Quint, Owner
Marla@TumbleTrips.example
Cell Phone Number 555-218-4603
Office Phone Number 555-647-1925
Specializing in Glimmerland destinations, Pelican Bay Fun Park, Cruises and All-Inclusive Vacations.

Nice but not required:
www.TumbleTrips.example
Facebook, Instagram, Twitter icons with username: TumbleTrips

Font styles to use
Sans Serif

Requirements
Must have
• Please try to use the colors from the logo as much as possible. I understand lighter shades/colors may be needed for some things.
Should not have
• NO SERIF FONTS. That is really the only thing I do not want at all

```html
<!DOCTYPE html>
<html lang="en">
<head>
<meta charset="utf-8">
<title>Tumble Trips – Business Card</title>
<link rel="stylesheet" href="https://fonts.googleapis.com/css2?family=Lato:wght@400;700&family=Satisfy&display=swap">
<style>
  :root {
    --navy: #151a3a;
    --navy-deep: #0f1330;
    --teal: #1ec3ad;
    --white: #ffffff;
    --silver: #c9ccd6;
    --page: #e9e7e2;
    --text-light: #e8eaf2;
  }
  * { box-sizing: border-box; margin: 0; padding: 0; }
  html, body { width: 1200px; height: 780px; overflow: hidden; }
  body {
    background: var(--page);
    font-family: "Lato", sans-serif;
    display: flex;
    align-items: center;
    justify-content: center;
    gap: 40px;
  }
  .card {
    position: relative;
    width: 560px;
    height: 320px;
    border-radius: 24px;
    overflow: hidden;
    background: var(--navy);
    box-shadow: 0 10px 28px rgba(0,0,0,.25);
  }
  .card-front__bg { position: absolute; inset: 0; }
  .brand {
    position: absolute;
    display: flex;
    align-items: center;
    gap: 12px;
  }
  .brand__dot { border-radius: 50%; background: var(--teal); }
  .brand__name { font-family: "Lato", sans-serif; font-weight: 700; letter-spacing: .5px; }
  .card-front .brand { left: 250px; top: 50px; }
  .card-front .brand__dot { width: 34px; height: 34px; }
  .card-front .brand__name { font-size: 30px; color: var(--navy); }

  .holder { position: absolute; left: 30px; top: 168px; width: 150px; }
  .holder__name {
    font-family: "Satisfy", "Lato", sans-serif;
    font-size: 26px;
    font-weight: 400;
    color: var(--white);
    line-height: 1.1;
    white-space: nowrap;
  }
  .holder__title {
    font-family: "Lato", sans-serif;
    font-size: 13px;
    color: var(--teal);
    margin-top: 4px;
    margin-left: 18px;
  }

  .tab {
    position: absolute; left: -14px; top: 250px;
    width: 28px; height: 28px; border-radius: 50%;
    background: var(--teal);
  }

  .contacts { position: absolute; left: 200px; top: 160px; list-style: none; }
  .contacts li {
    display: flex; align-items: center; gap: 8px;
    font-size: 12.5px; color: var(--text-light);
    height: 18px;
    white-space: nowrap;
  }
  .contacts svg { width: 13px; height: 13px; flex: none; }

  .specialty {
    position: absolute; left: 200px; top: 240px;
    font-size: 12.5px; line-height: 17px; color: var(--text-light);
    white-space: nowrap;
  }
  .specialty strong { color: var(--teal); font-weight: 700; }

  .social {
    position: absolute; left: 200px; top: 283px;
    display: flex; align-items: center; gap: 6px;
  }
  .social__box { width: 18px; height: 18px; background: var(--teal); border-radius: 2px; }
  .social__handle { font-size: 12.5px; font-weight: 700; color: var(--text-light); margin-left: 8px; }

  .card-back {
    background: radial-gradient(ellipse at 45% 45%, #1c2250 0%, var(--navy) 55%, var(--navy-deep) 100%);
  }
  .card-back .brand {
    left: 0; right: 0; top: 0; bottom: 0;
    justify-content: center;
  }
  .card-back .brand__dot { width: 56px; height: 56px; background: var(--silver); }
  .card-back .brand__name { font-size: 48px; color: var(--silver); }
</style>
</head>
<body>

  <section class="card card-front" aria-label="Card front">
    <svg class="card-front__bg" viewBox="0 0 560 320" preserveAspectRatio="none" aria-hidden="true">
      <rect width="560" height="320" fill="var(--navy)"/>
      <path d="M0 0 H560 V40 C460 90 360 150 220 150 C140 150 70 142 0 152 V0 Z" fill="var(--teal)" transform="translate(0 10)"/>
      <path d="M0 0 H560 V40 C460 90 360 150 220 150 C140 150 70 142 0 152 V0 Z" fill="var(--white)"/>
    </svg>

    <div class="brand">
      <span class="brand__dot"></span>
      <span class="brand__name">Tumble Trips</span>
    </div>

    <span class="tab"></span>

    <div class="holder">
      <p class="holder__name">Marla Quint</p>
      <p class="holder__title">Owner</p>
    </div>

    <ul class="contacts">
      <li>
        <svg viewBox="0 0 14 14"><circle cx="7" cy="7" r="7" fill="var(--teal)"/><rect x="4.5" y="3" width="5" height="8" rx="1" fill="none" stroke="var(--white)" stroke-width="1.2"/></svg>
        555-218-4603
      </li>
      <li>
        <svg viewBox="0 0 14 14"><circle cx="7" cy="7" r="7" fill="var(--teal)"/><path d="M4 4.5 C4 8 6 10 9.5 10 L10 8.6 L8.5 7.8 L7.8 8.5 C6.6 8 6 7.4 5.5 6.2 L6.2 5.5 L5.4 4 Z" fill="var(--white)"/></svg>
        555-647-1925
      </li>
      <li>
        <svg viewBox="0 0 14 14"><circle cx="7" cy="7" r="7" fill="var(--teal)"/><rect x="3.5" y="4.5" width="7" height="5" fill="none" stroke="var(--white)" stroke-width="1"/><path d="M3.5 4.5 L7 7.3 L10.5 4.5" fill="none" stroke="var(--white)" stroke-width="1"/></svg>
        Marla@TumbleTrips.example
      </li>
      <li>
        <svg viewBox="0 0 14 14"><circle cx="7" cy="7" r="7" fill="var(--teal)"/><circle cx="7" cy="7" r="3.8" fill="none" stroke="var(--white)" stroke-width="1"/><path d="M3.2 7 H10.8 M7 3.2 V10.8" stroke="var(--white)" stroke-width="0.8"/></svg>
        www.TumbleTrips.example
      </li>
    </ul>

    <p class="specialty">
      <strong>Specializing in</strong> Glimmerland destinations,<br>
      Pelican Bay Fun Park | Cruises and All-Inclusive Vacations.
    </p>

    <div class="social">
      <span class="social__box"></span>
      <span class="social__box"></span>
      <span class="social__box"></span>
      <span class="social__handle">TumbleTrips</span>
    </div>
  </section>

  <section class="card card-back" aria-label="Card back">
    <div class="brand">
      <span class="brand__dot"></span>
      <span class="brand__name">Tumble Trips</span>
    </div>
  </section>

</body>
</html>
```